E-learning Information & Community Website Needs a Makeover

I'm looking for a design makeover for my website "Tavipor.club". Tavipor's aim is to connect people to online learning through forums, information, guides & independent reviews. The site was launched in September 2014 using a forum software (Xenforo), but now needs a more polished and sophisticated look which communicates expertise and professionalism. I would like to see designs that use the current "Tavipor" blue (#0070c0). To visit the current website, go to http://www.tavipor.club/

Target Market(s)

People wishing to study online

Industry/Entity Type

Club

Number of Pages Required

4 page

Font styles to use
Sans Serif

Requirements
Must have
• A simple, clear and sophisticated lading page with links to the site's key features: discussion forums, Useful resources, Reviews, News etc, Articles. (See layout idea file attached)
• The main pages are the Landing Page, Discussion Forums, Resources & Reviews
• I would like to see designs that use the current "Tavipor" blue (#0070c0).
Nice to have
• Something uncluttered and easy to understand. The design should convey expertise in the field of online learning, giving users a sense of trust in the site's offerings.
• To give an idea of the sort of thing I'm after, take a look at wendricast.com website (screenshot attached)

```html
<!DOCTYPE html>
<html lang="en">
<head>
<meta charset="utf-8">
<title>Tavipor – Connecting People to Online Learning</title>
<link href="https://fonts.googleapis.com/css2?family=Open+Sans:ital,wght@0,400;0,600;1,400&display=swap" rel="stylesheet">
<style>
:root{
  --brand:#0070c0;
  --ink:#111;
  --bar:#1a1a1a;
  --text:#222;
  --muted:#999;
  --link:#1e9ad6;
  --panel:#f1f1f1;
  --rule:#e2e2e2;
  --tag-article:#e5201f;
  --tag-courses:#f5a000;
  --tag-news:#c8c8c8;
  --tag-event:#8c8c8c;
  --tag-advice:#7ed56f;
}
*{box-sizing:border-box;margin:0;padding:0}
html,body{width:960px;height:1200px;overflow:hidden}
body{position:relative;background:#fff;font-family:"Open Sans",Arial,sans-serif;color:var(--text)}
a{text-decoration:none;color:inherit}

.topbar{position:absolute;left:0;top:0;width:960px;height:34px;background:var(--bar)}
.brand{position:absolute;left:181px;top:-3px;color:#9fd0f2;font-size:20px;line-height:22px}
.brand small{display:block;color:#fff;font-size:8.5px;line-height:10px;margin-top:1px}
.main-nav{position:absolute;left:373px;top:11px;display:flex;gap:12px;font-size:9px;color:#aaa}
.main-nav .current{color:#fff}
.main-nav .login{color:var(--link);margin-left:6px}

.hero{position:absolute;left:0;top:34px;width:960px;height:197px;
  background:linear-gradient(180deg,#1e9be0 0%,#2aa9ea 60%,#5aaed0 85%,#4b8a9c 100%);
  border-bottom:3px solid var(--ink)}
.hero h1{position:absolute;left:192px;top:22px;font-weight:400;font-size:26px;line-height:30px;color:#fff}
.hero .signup{position:absolute;left:195px;top:105px;width:125px;height:30px;border-radius:15px;background:#1e1e1e;
  color:#fff;font-style:italic;font-size:14px;line-height:30px;text-align:center}

.features{position:absolute;left:0;top:234px;width:960px;height:259px;background:var(--panel)}
.tiles{position:absolute;left:174px;top:17px;display:grid;grid-template-columns:repeat(3,198px);grid-auto-rows:105px;gap:8px 7px}
.tile{background:var(--brand);border:2px solid #0b2740;border-radius:8px;color:#fff;display:flex;flex-direction:column;align-items:center;justify-content:center;gap:6px;font-size:21px}
.tile svg{width:36px;height:36px}

.section-title{position:absolute;left:0;width:960px;text-align:center;font-weight:400;font-size:25px;color:#111}
.topics-title{top:507px}
.topics{position:absolute;left:176px;top:544px;width:645px;height:56px;background:#f8f8f8;display:flex;align-items:center;justify-content:space-between;padding:0 10px;color:#9a9a9a;font-size:13px;white-space:nowrap}
.topics > *{flex-shrink:0;display:block}
.topics .arrow{width:0;height:0;border-top:5px solid transparent;border-bottom:5px solid transparent}
.topics .prev{border-right:7px solid #000}
.topics .next{border-left:7px solid #000}
.topics .round{width:34px;height:34px;border-radius:50%;background:#ccc}
.topics .square{width:22px;height:34px;background:#ccc}

.community-title{top:638px}
.threads-head{position:absolute;left:0;top:682px;width:960px;height:28px;background:var(--brand);border-top:2px solid #123;border-bottom:2px solid #123;color:#fff;font-size:11px}
.threads-head span{position:absolute;top:6px}

.threads{position:absolute;left:183px;top:714px;width:599px;list-style:none}
.thread{position:relative;height:44px;border-bottom:1px solid var(--rule)}
.avatar{position:absolute;left:0;top:7px;width:30px;height:30px;border-radius:4px;background:var(--brand);color:#fff;font-size:7px;line-height:30px;text-align:center}
.avatar.member{background:#9c7f6a}
.avatar.blank{background:#eee;border:1px solid #ddd}
.title{position:absolute;left:42px;top:7px;width:315px;font-size:12px;line-height:14px;color:var(--link);white-space:nowrap}
.tag{display:inline-block;padding:0 4px;margin-right:3px;border-radius:2px;font-size:9.5px;line-height:12px;color:#111;vertical-align:1px}
.tag.article{background:var(--tag-article);color:#fff}
.tag.courses{background:var(--tag-courses)}
.tag.news{background:var(--tag-news)}
.tag.event{background:var(--tag-event)}
.tag.advice{background:var(--tag-advice)}
.meta{position:absolute;left:42px;bottom:6px;font-size:8.5px;line-height:10px;color:var(--muted);white-space:nowrap}
.stats{position:absolute;left:363px;top:6px;width:105px;height:32px;border-left:1px solid var(--rule);padding-left:8px;font-size:11px;color:var(--muted)}
.stats div{display:flex;justify-content:space-between}
.stats b{font-weight:400;color:#222}
.stats .views{font-size:8.5px}
.last{position:absolute;right:3px;top:8px;text-align:right;color:var(--link);font-size:12px;line-height:14px}
.last small{display:block;color:var(--muted);font-size:8.5px}
.tall{height:48px}
.tall .title{top:3px;width:260px;white-space:normal}
.tall .stats,.tall .last{top:8px}
.tall .avatar{top:9px}

.pager{position:absolute;left:767px;top:1090px;display:flex;gap:4px}
.pager i{width:0;height:0;border-top:5px solid transparent;border-bottom:5px solid transparent}
.pager .prev{border-right:7px solid #000}
.pager .next{border-left:7px solid #000}

.footer{position:absolute;left:0;top:1117px;width:960px;height:83px;background:var(--bar)}
.social{position:absolute;left:266px;top:18px;display:flex;gap:2px}
.social span{width:15px;height:15px;border-radius:50%;background:#4a6fb5}
.social span:nth-child(2){background:#2aa3e0}
.social span:nth-child(3){background:#d8261f}
.social span:nth-child(4){background:#dc4a38}
.newsletter{position:absolute;left:358px;top:12px;display:flex;align-items:center;gap:10px}
.newsletter .field{width:240px;height:21px;background:#fff;font-style:italic;font-size:9px;line-height:21px;padding-left:8px;color:#111}
.newsletter .go{color:var(--link);font-style:italic;font-size:9px}
.foot-nav{position:absolute;left:269px;top:54px;display:flex;gap:11px;font-size:9px;color:#aaa}
.foot-nav .current{color:#fff}
.foot-nav .login{color:var(--link);margin-left:6px}
</style>
</head>
<body>

<header class="topbar">
  <a class="brand" href="#">Tavipor<small>Connecting People to Online Learning</small></a>
  <nav class="main-nav">
    <a class="current" href="#">Home</a><a href="#">Forums</a><a href="#">Resources</a><a href="#">Members</a><a href="#">FAQ</a><a href="#">Blog</a><a href="#">Tavipor Español</a><a href="#">Lumen Scoop</a><a class="login" href="#">Login</a>
  </nav>
</header>

<section class="hero" role="img" aria-label="Photo of a student with a laptop stretching arms on a grassy hill under a blue sky">
  <h1>At the heart of connecting people<br>to online learning</h1>
  <a class="signup" href="#">Signup for free</a>
</section>

<section class="features">
  <div class="tiles">
    <a class="tile" href="#">
      <svg viewBox="0 0 24 24" fill="#cfe6f7"><path d="M10 1h4l.6 3 2 .9 2.6-1.7 2.8 2.8-1.7 2.6.9 2 3 .6v4l-3 .6-.9 2 1.7 2.6-2.8 2.8-2.6-1.7-2 .9-.6 3h-4l-.6-3-2-.9-2.6 1.7-2.8-2.8 1.7-2.6-.9-2-3-.6v-4l3-.6.9-2L3.9 6l2.8-2.8 2.6 1.7 2-.9z"/><circle cx="12" cy="12" r="3.5" fill="#0070c0"/></svg>
      Getting Started</a>
    <a class="tile" href="#">
      <svg viewBox="0 0 24 24"><circle cx="12" cy="12" r="11" fill="#cfe6f7"/><circle cx="7" cy="12" r="1.8" fill="#0070c0"/><circle cx="12" cy="12" r="1.8" fill="#0070c0"/><circle cx="17" cy="12" r="1.8" fill="#0070c0"/></svg>
      Discussions</a>
    <a class="tile" href="#">
      <svg viewBox="0 0 24 24"><path d="M1 12C4 6 8 4 12 4s8 2 11 8c-3 6-7 8-11 8S4 18 1 12z" fill="none" stroke="#cfe6f7" stroke-width="2"/><circle cx="12" cy="12" r="4" fill="#cfe6f7"/></svg>
      Reviews</a>
    <a class="tile" href="#">
      <svg viewBox="0 0 24 24" fill="#cfe6f7"><path d="M7 11V4a1.3 1.3 0 0 1 2.6 0v6h.5V2.5a1.3 1.3 0 0 1 2.6 0V10h.5V3.5a1.3 1.3 0 0 1 2.6 0V11h.5V6a1.3 1.3 0 0 1 2.6 0v9c0 4-3 7-7 7s-5-2-7-5l-2.5-4a1.3 1.3 0 0 1 2.2-1.3z"/></svg>
      Tips &amp; Guidelines</a>
    <a class="tile" href="#">
      <svg viewBox="0 0 24 24"><path d="M20 7A10 10 0 1 0 22 12" fill="none" stroke="#cfe6f7" stroke-width="2"/><path d="M17 3l4 4-5 1z" fill="#cfe6f7"/><text x="12" y="15" text-anchor="middle" font-size="8" font-family="Open Sans, sans-serif" font-weight="600" fill="#cfe6f7">24</text></svg>
      News &amp; Articles</a>
    <a class="tile" href="#">
      <svg viewBox="0 0 24 24" fill="#cfe6f7"><path d="M3 2h9v3H6v14H3z"/><path d="M8 6h8l5 5v12H8z"/></svg>
      Newsletter</a>
  </div>
</section>

<h2 class="section-title topics-title">Frequent Topics</h2>
<div class="topics">
  <i class="arrow prev"></i>
  <span class="round"></span>
  <span>Harrow Vale</span>
  <span>Kelmor Schools</span>
  <span>Orvant</span>
  <span>Fenwick College</span>
  <span>Ashmere Global</span>
  <span class="square"></span>
  <i class="arrow next"></i>
</div>

<h2 class="section-title community-title">From the Community</h2>
<div class="threads-head">
  <span style="left:193px">Recent Threads</span>
  <span style="left:493px">Start Date</span>
  <span style="left:555px">Replies</span>
  <span style="left:636px">Views</span>
  <span style="left:676px">Last Message</span>
</div>

<ul class="threads">
  <li class="thread tall">
    <span class="avatar member"></span>
    <a class="title" href="#"><span class="tag article">Article</span>Wellcom to Velarx, the new catalan MOOC directory</a>
    <span class="meta">Marcel Oriol, Yesterday at 7:02 PM, Blog</span>
    <div class="stats"><div>Replies: <b>0</b></div><div class="views">Views: <b>28</b></div></div>
    <div class="last">Marcel Oriol<small>Yesterday at 7:02 PM</small></div>
  </li>
  <li class="thread">
    <span class="avatar">Tavipor</span>
    <a class="title" href="#"><span class="tag courses">Courses</span>Norvane MOOCs</a>
    <span class="meta">Delphine, Yesterday at 9:30 AM, Qedro</span>
    <div class="stats"><div>Replies: <b>0</b></div><div class="views">Views: <b>55</b></div></div>
    <div class="last">Delphine<small>Yesterday at 9:30 AM</small></div>
  </li>
  <li class="thread">
    <span class="avatar">Tavipor</span>
    <a class="title" href="#"><span class="tag news">News</span>Tavipor's Lumen Scoop promoted to Gold level!</a>
    <span class="meta">Delphine, Monday at 6:24 PM, MOOC News</span>
    <div class="stats"><div>Replies: <b>1</b></div><div class="views">Views: <b>47</b></div></div>
    <div class="last">Ravik<small>Tuesday at 2:14 PM</small></div>
  </li>
  <li class="thread">
    <span class="avatar">Tavipor</span>
    <a class="title" href="#"><span class="tag news">News</span>Kestrel Academy are looking for a video star!</a>
    <span class="meta">Delphine, Tuesday at 8:41 AM, General stuff on course providers</span>
    <div class="stats"><div>Replies: <b>0</b></div><div class="views">Views: <b>116</b></div></div>
    <div class="last">Delphine<small>Tuesday at 8:41 AM</small></div>
  </li>
  <li class="thread">
    <span class="avatar">Tavipor</span>
    <a class="title" href="#"><span class="tag event">Event</span>What Reviews divulge about Online Education</a>
    <span class="meta">Delphine, Monday at 10:52 AM, Events</span>
    <div class="stats"><div>Replies: <b>0</b></div><div class="views">Views: <b>76</b></div></div>
    <div class="last">Delphine<small>Monday at 10:52 AM</small></div>
  </li>
  <li class="thread tall">
    <span class="avatar blank"></span>
    <a class="title" href="#"><span class="tag advice">Advice</span>How do you "unenroll" from a course on Corvista?</a>
    <span class="meta">Miriam, Feb 13, 2015, MOOC Advice</span>
    <div class="stats"><div>Replies: <b>2</b></div><div class="views">Views: <b>3,482</b></div></div>
    <div class="last">Owen<small>Sunday at 11:01 PM</small></div>
  </li>
  <li class="thread">
    <span class="avatar">Tavipor</span>
    <a class="title" href="#"><span class="tag courses">Courses</span>6 top rated free courses starting in May</a>
    <span class="meta">Delphine, May 13, 2015, Recommend a course here</span>
    <div class="stats"><div>Replies: <b>0</b></div><div class="views">Views: <b>152</b></div></div>
    <div class="last">Delphine<small>May 13, 2015</small></div>
  </li>
  <li class="thread">
    <span class="avatar">Tavipor</span>
    <a class="title" href="#"><span class="tag news">News</span>The European MOOCs Scoreboard</a>
    <span class="meta">Delphine, May 12, 2015, MOOC News</span>
    <div class="stats"><div>Replies: <b>0</b></div><div class="views">Views: <b>105</b></div></div>
    <div class="last">Delphine<small>May 12, 2015</small></div>
  </li>
</ul>

<div class="pager"><i class="prev"></i><i class="next"></i></div>

<footer class="footer">
  <div class="social"><span></span><span></span><span></span><span></span></div>
  <div class="newsletter"><span class="field">Subscribe for Monthly Newsletter</span><a class="go" href="#">Subscribe</a></div>
  <nav class="foot-nav">
    <a class="current" href="#">Home</a><a href="#">Forums</a><a href="#">Resources</a><a href="#">Members</a><a href="#">FAQ</a><a href="#">Blog</a><a href="#">Tavipor Español</a><a href="#">Lumen Scoop</a><a class="login" href="#">Login</a>
  </nav>
</footer>

</body>
</html>
```